Brochure for a civil enineering company in A4 format

I need a brochure design for our company TIRO Engineering S.r.l.. We are an engineering consultant company. Our main clients are from the infrastructure industry (geotechnical and underground sectors mainly).
We are looking for a 2 pages (4 faces) fold out design with a glued pocket where we can put individual data sheets.
I need A4 format pages.

Target Market(s)

We are an engineering consultant company. Our main clients are from the infrastructure industry (geotechnical and underground sectors mainly).

Industry/Entity Type

Civil Engineer

Font styles to use
Sans Serif

Requirements
Must have
• Overall: 2 pages in A4 format
Essential style. Bright and modern appearance.
Glued pocket
Logo integrated in a picture on the pocket where I would like to insert a slogan (… tiro engineering … reliable solutions …)
Attached are selected images which the designer can use and edit at their own discretion.
Some advice in the following (anyway designers are free to provide their solutions):
Outer sheets:
Front page with name, logo. It could be nice to have the “m” of the logo integrated in a pictures, also a modified picture (I mean modify one of the attached pictures) so to create a general image and do not tie the cover to a specific job.
Back page: offices address and contact email address. Nice to have one space for a slogan.
Inner sheet: text that I upload in the file “inside-sheets”, possibly with pictures on each sheet. In the right faces insert the glued pocket. On this pages insert the section OUR EXPERIENCE ….with a space for a picture of our team.
Nice to have
• Clean and essential design.
Pictures choosing from the atteched ones. Pictures could be modified in a very light manner to make them a general idea of the work ( I mean geotechnical world) without to be immediately linked to a specific site.
Should not have
• excessive frills

```html
<!DOCTYPE html>
<html lang="it">
<head>
<meta charset="utf-8">
<title>TIRO Engineering – Brochure</title>
<link href="https://fonts.googleapis.com/css2?family=Montserrat:wght@300;400;500;600;700&display=swap" rel="stylesheet">
<style>
:root{
  --stage:#5c5c5c;
  --paper:#ededed;
  --paper-light:#f6f6f6;
  --paper-mid:#e4e4e4;
  --ink:#2b2b2b;
  --ink-soft:#555;
  --rule:#6a6a6a;
  --hatch:#d6d6d6;
  --band:#1c1c1c;
}
*{margin:0;padding:0;box-sizing:border-box}
html,body{width:1148px;height:1200px;overflow:hidden}
body{background:var(--stage);font-family:"Montserrat",sans-serif;color:var(--ink);position:relative}
.spread{position:absolute;left:34px;width:1080px;height:508px;background:var(--paper);overflow:hidden}
.spread--outer{top:60px}
.spread--inner{top:632px}
.panel{position:absolute;top:0;width:360px;height:508px}
.panel--1{left:0;background:linear-gradient(180deg,#ebebeb,#f1f1f1)}
.panel--2{left:360px;background:linear-gradient(180deg,#e9e9e9,#efefef);box-shadow:inset 1px 0 0 rgba(0,0,0,.05)}
.panel--3{left:720px;background:var(--paper-light);box-shadow:inset 1px 0 0 rgba(0,0,0,.05)}
.abs{position:absolute}
.section-title{position:absolute;font-size:14px;letter-spacing:.3px;font-weight:700;color:var(--ink);text-transform:uppercase;padding-bottom:5px;border-bottom:1px solid var(--rule)}
.section-title .light{font-weight:300}
.body-text{position:absolute;font-size:5.6px;line-height:1.52;color:var(--ink-soft);text-align:justify}
.body-text p{margin-bottom:7px}
.body-text p:last-child{margin-bottom:0}
.body-text strong{color:var(--ink);font-weight:600}
.tone-block{position:absolute;background:var(--hatch)}
.photo{position:absolute}
.photo--framed{outline:4px solid #fff}
.contacts{position:absolute;font-size:7.2px;line-height:1.42;font-weight:500;color:var(--ink)}
.contacts .office{margin-bottom:10px}
.contacts .row{display:flex;align-items:center;gap:4px}
.contacts .row svg{width:7px;height:7px;flex:none}
.contacts .pad{padding-left:11px}
.wordmark{position:absolute;font-weight:600;color:var(--ink);letter-spacing:-1px;line-height:1}
.wordmark-tag{position:absolute;font-size:2.6px;letter-spacing:.6px;color:var(--ink-soft);text-transform:uppercase}
.slogan{position:absolute;font-size:12.6px;font-weight:600;letter-spacing:.2px;color:var(--ink);text-transform:uppercase}
.founders-band{position:absolute;left:396px;top:102px;width:288px;height:15px;border-bottom:1px solid var(--rule)}
.founders-band svg{position:absolute;left:0;top:0}
.founders-band span{position:absolute;left:9px;top:2px;font-size:8.4px;font-weight:600;color:#fff;letter-spacing:.4px}
.dark-band{position:absolute;left:0;top:0}
</style>
</head>
<body>

<!-- Outer sheet: company, offices, cover -->
<section class="spread spread--outer">
  <div class="panel panel--1">
    <h2 class="section-title" style="left:37px;top:36px;width:286px"><span class="light">Our </span>Company</h2>
    <div class="body-text" style="left:37px;top:72px;width:286px">
      <p>TIRO Engineering S.r.l. offre servizi di consulenza tecnica, contrattuale e strategica ai principali attori nei settori delle scienze geologiche, dell'ingegneria geotecnica e dell'ingegneria idraulica. Lavoriamo per mitigare il rischio e ridurre l'incertezza, con flessibilità nella ricerca della soluzione ottimale contribuendo ad aumentare la redditività del progetto.</p>
      <p>TIRO Engineering S.r.l. è una società indipendente che nasce nel luglio 2020 dall'associazione di un gruppo di professionisti che hanno messo a fattor comune la reciproca esperienza maturata in oltre trent'anni di attività come progettisti e consulenti nel settore delle grandi opere di ingegneria civile lavorando come Direttori Tecnici di Main Engineering Companies and as Freelancers.</p>
      <p>TIRO Engineering S.r.l. vuole unire l'esperienza dei Fondatori e delle figure chiave con l'entusiasmo di chi intraprende una nuova attività, per dare vita ad una nuova realtà che si pone come obbiettivo principale il design of infrastructures that are safe, sustainable and economic.</p>
      <p>Each of our projects represents a long term commitment, we believe in providing safe, reliable, sustainable and innovative solutions. This is and will be our distinctive characteristic.</p>
    </div>
    <div class="tone-block" style="left:143px;top:308px;width:180px;height:178px"></div>
    <div class="photo" role="img" aria-label="Photo of a deep urban excavation with reinforced slab and workers" style="left:38px;top:236px;width:208px;height:228px;background:linear-gradient(180deg,#a9c6e0 0%,#b8a996 22%,#9d968c 45%,#c9c6c0 70%,#8f8a84 100%)"></div>
  </div>

  <div class="panel panel--2">
    <div class="tone-block" style="left:110px;top:41px;width:178px;height:178px;background:#dedede"></div>
    <h2 class="section-title" style="left:36px;top:315px;width:160px"><span class="light">Our </span>Offices</h2>
    <div class="contacts" style="left:36px;top:343px">
      <div class="office">
        <div class="pad">Milano</div>
        <div class="row"><svg viewBox="0 0 10 10"><path d="M5 1a2.6 2.6 0 0 1 2.6 2.6C7.6 5.6 5 9 5 9S2.4 5.6 2.4 3.6A2.6 2.6 0 0 1 5 1z" fill="none" stroke="#2b2b2b" stroke-width="1"/><circle cx="5" cy="3.6" r=".9" fill="#2b2b2b"/></svg>Via Verdi, 14</div>
        <div class="pad">20121 Milano - IT</div>
        <div class="row" style="margin-top:3px"><svg viewBox="0 0 10 10"><circle cx="5" cy="5" r="4.2" fill="none" stroke="#2b2b2b" stroke-width=".9"/><path d="M3.5 3c.3 1.8 1.4 3.1 3.2 3.7l.6-.8-1-.6-.5.4c-.6-.3-1-.8-1.3-1.4l.4-.5-.6-1z" fill="#2b2b2b"/></svg>+39 02 555 01234</div>
        <div class="row"><svg viewBox="0 0 10 10"><rect x="1" y="2.5" width="8" height="5.5" fill="none" stroke="#2b2b2b" stroke-width=".9"/><path d="M1 2.5l4 3 4-3" fill="none" stroke="#2b2b2b" stroke-width=".9"/></svg>info@tiroengineering.example</div>
      </div>
      <div class="office">
        <div class="pad">Arco TN</div>
        <div class="row"><svg viewBox="0 0 10 10"><path d="M5 1a2.6 2.6 0 0 1 2.6 2.6C7.6 5.6 5 9 5 9S2.4 5.6 2.4 3.6A2.6 2.6 0 0 1 5 1z" fill="none" stroke="#2b2b2b" stroke-width="1"/><circle cx="5" cy="3.6" r=".9" fill="#2b2b2b"/></svg>Via S. Marco, 9</div>
        <div class="pad">38062 Arco TN - IT</div>
        <div class="row" style="margin-top:3px"><svg viewBox="0 0 10 10"><circle cx="5" cy="5" r="4.2" fill="none" stroke="#2b2b2b" stroke-width=".9"/><path d="M3.5 3c.3 1.8 1.4 3.1 3.2 3.7l.6-.8-1-.6-.5.4c-.6-.3-1-.8-1.3-1.4l.4-.5-.6-1z" fill="#2b2b2b"/></svg>+39 0464 555 098</div>
        <div class="row"><svg viewBox="0 0 10 10"><rect x="1" y="2.5" width="8" height="5.5" fill="none" stroke="#2b2b2b" stroke-width=".9"/><path d="M1 2.5l4 3 4-3" fill="none" stroke="#2b2b2b" stroke-width=".9"/></svg>info@tiroengineering.example</div>
      </div>
      <div class="row"><svg viewBox="0 0 10 10"><circle cx="5" cy="5" r="4" fill="none" stroke="#2b2b2b" stroke-width=".9"/><ellipse cx="5" cy="5" rx="1.8" ry="4" fill="none" stroke="#2b2b2b" stroke-width=".7"/><path d="M1 5h8" stroke="#2b2b2b" stroke-width=".7"/></svg>www.tiroengineering.example</div>
    </div>
    <div class="wordmark" style="left:243px;top:452px;font-size:22px">tiro</div>
    <div class="wordmark-tag" style="left:243px;top:475px">tiro engineering · reliable solutions</div>
  </div>

  <div class="panel panel--3">
    <div class="wordmark" style="left:109px;top:34px;font-size:46px">tiro</div>
    <div class="slogan" style="left:37px;top:443px">TIRO Engineering, Reliable Solutions</div>
  </div>

  <div class="photo photo--framed" role="img" aria-label="Photo of a large tunnel excavation with twin vaults in deep blue and violet light" style="left:604px;top:113px;width:291px;height:284px;background:radial-gradient(ellipse at 55% 55%,#6f6aa8 0%,#3f3d78 45%,#26264f 100%)"></div>
  <div class="photo" role="img" aria-label="Aerial photo of a construction site with an orange crane and materials" style="left:900px;top:113px;width:175px;height:156px;background:linear-gradient(160deg,#b9b0a3,#8e8579 55%,#a29383)"></div>
  <div class="photo" role="img" aria-label="Aerial photo of a site yard with sheds among green vegetation" style="left:900px;top:274px;width:175px;height:123px;background:linear-gradient(160deg,#6f8a52,#b3b0a7 45%,#9c9a92 70%,#5d7a44)"></div>
</section>

<!-- Inner sheet: services, expertise, pocket -->
<section class="spread spread--inner">
  <div class="panel panel--1">
    <h2 class="section-title" style="left:37px;top:32px;width:286px"><span class="light">Our </span>Services</h2>
    <div class="body-text" style="left:37px;top:58px;width:286px">
      <p>Progettazione e consulenza specialistica nel campo della geologia, dell'ingegneria geotecnica, delle opere sotterranee e dell'ingegneria idraulica.</p>
      <p>Aiutiamo i nostri clienti a risolvere problemi di natura progettuale, contrattuale e costruttiva che possono nascere nell'intera vita del progetto portando la nostra esperienza all'interno delle loro organizzazioni, migliorando la qualità dei loro servizi di ingegneria, ottimizzando i loro progetti, proponendo nuove idee e soluzioni, rafforzando i loro approcci ......</p>
      <p>TIRO Engineering è in grado di fornire la propria assistenza nell'intero iter procedurale, dalla fase di indagine preliminare e di analisi di fattibilità fino alla progettazione costruttiva e all'assistenza tecnica in fase realizzativa.</p>
    </div>
    <div class="photo" role="img" aria-label="Photo of an excavator working below a historic railway station building" style="left:38px;top:155px;width:284px;height:105px;background:linear-gradient(180deg,#b6c6d6 0%,#c9a98f 30%,#5e5750 55%,#a39e94 100%)"></div>
    <div class="body-text" style="left:37px;top:271px;width:286px"><p><strong>La specializzazione e l'esperienza accumulate nelle discipline della geologia, dell'ingegneria geotecnica e del sottosuolo e dell'idraulica ci permette di massimizzare la nostra efficacia quando sia necessario:</strong></p></div>
    <div class="tone-block" style="left:25px;top:345px;width:52px;height:60px"></div>
    <div class="photo" role="img" aria-label="Photo of a shaft excavation with concrete walls" style="left:38px;top:311px;width:101px;height:84px;background:linear-gradient(180deg,#a29c94,#6d675f 60%,#8d8679)"></div>
    <div class="body-text" style="left:160px;top:315px;width:162px">
      <p>far fronte a situazioni di emergenza anche su progetti in fase di sviluppo avanzato garantendo l'immediata focalizzazione delle problematiche di progetto e garantendo il risultato finale atteso (in termini di qualità, tempistiche e costi...)</p>
      <p>fornire "second opinion" di elevato valore tecnico ed amministrativo in occasione di problematiche progettuali e costruttive e dispute legali</p>
    </div>
    <div class="body-text" style="left:37px;top:415px;width:170px">
      <p>analizzare in tempi brevi progetti svolti da terzi individuandone le "criticità", verificandone la cantierabilità e la validità tecnico economica.</p>
      <p>ottimizzare i progetti redatti da terzi implementandone il contenuto e massimizzando l'efficacia economica degli investimenti.</p>
    </div>
    <div class="tone-block" style="left:232px;top:445px;width:104px;height:52px"></div>
    <div class="photo" role="img" aria-label="Photo of a tunnel face under excavation with lights" style="left:221px;top:404px;width:101px;height:82px;background:radial-gradient(ellipse at 50% 60%,#b69472,#5a4838 55%,#2e261f)"></div>
  </div>

  <div class="panel panel--2">
    <h2 class="section-title" style="left:36px;top:32px;width:285px"><span class="light">Our </span>Expertise and Experience</h2>
    <div class="body-text" style="left:36px;top:61px;width:285px"><p>La società nasce dall'associazione di un gruppo di professionisti, con indiscusse competenze ed affidabilità, con esperienza maturata in oltre trent'anni di attività come progettisti e consulenti nel settore delle grandi opere di ingegneria civile; geologia, ingegneria geotecnica ed idraulica ed opere sotterranee sono il "core" delle loro competenze....</p></div>
    <div class="body-text" style="left:36px;top:124px;width:287px;font-size:5.1px"><p>Marco. Già Direttore Tecnico e Socio di ALFA Srl fino al dicembre 2018, ha firmato gran parte dei progetti nel campo delle opere sotterranee e della geotecnica. Dal gennaio 2019 è Direttore Tecnico di BETA. Vanta più di 150 gallerie naturali progettate e numerose assistenze tecniche in corso d'opera, per imprese di costruzione e committenti pubblici, con opere il cui valore supera i 440 Mio EUR e servizi di progettazione definitiva ed esecutiva per opere il cui valore supera i 1.400 Mio EUR, in Italia e all'estero, per progetti il cui valore complessivo supera i 3.400 Mio EUR.</p></div>
    <div class="photo" role="img" aria-label="Group photo of the company team" style="left:38px;top:195px;width:285px;height:110px;background:linear-gradient(180deg,#d9d4c6 0%,#b7aca0 40%,#6a7f9c 75%,#4c5f7e 100%)"></div>
    <div class="body-text" style="left:36px;top:316px;width:287px;font-size:5.1px">
      <p>Luca 30 anni di esperienza professionale. Coinvolto in più di 150 gallerie naturali con lunghezza complessiva superiore a 360 km. Numerosi progetti ed attività di assistenza tecnica nel campo delle strutture, delle sistemazioni idrogeologiche e dei versanti e delle opere di protezione ambientale, per opere il cui valore supera i 440 Mio EUR e servizi di progettazione per opere oltre i 1.400 Mio EUR, in Italia e all'estero.</p>
      <p>Giulia 30 anni di esperienza professionale. Coinvolta in più di 150 gallerie naturali con lunghezza complessiva superiore a 360 km. Numerosi progetti ed attività di assistenza tecnica nel campo delle strutture, delle sistemazioni idrogeologiche e dei versanti e delle opere di protezione ambientale, per opere il cui valore supera i 440 Mio EUR e servizi di verifica ai fini della validazione, in Italia e all'estero.</p>
      <p>Elena 30 anni di esperienza professionale. Coinvolta in più di 150 gallerie naturali con lunghezza complessiva superiore a 360 km. Numerosi progetti ed attività di assistenza tecnica nel campo delle strutture, delle sistemazioni idrogeologiche e dei versanti e delle opere di protezione ambientale, per opere il cui valore supera i 440 Mio EUR e progetti complessivi oltre i 3.400 Mio EUR.</p>
    </div>
  </div>

  <div class="founders-band">
    <svg width="160" height="15" viewBox="0 0 160 15"><path d="M0 0H148L156 15H0Z" fill="var(--band)"/></svg>
    <span>I SOCI FONDATORI SONO:</span>
  </div>

  <div class="panel panel--3">
    <div class="photo" role="img" aria-label="Photo of a lit tunnel interior with ribbed lining" style="left:33px;top:39px;width:158px;height:155px;background:radial-gradient(ellipse at 50% 60%,#c9cbe0 0%,#6b6c9a 35%,#2c2d58 100%)"></div>
    <div class="photo" role="img" aria-label="Photo of a stepped slope excavation beside a wooded hill" style="left:203px;top:39px;width:124px;height:155px;background:linear-gradient(170deg,#5d7d45 0%,#7d8d62 35%,#b7b2a8 65%,#cfcbc3 100%)"></div>
    <div class="photo" role="img" aria-label="Photo of twin tunnel portals under construction with a crane" style="left:33px;top:205px;width:294px;height:154px;background:linear-gradient(180deg,#c4d2dd 0%,#7b8670 30%,#9a9184 55%,#4f4a45 100%)"></div>
  </div>

  <svg class="dark-band" width="1080" height="508" viewBox="0 0 1080 508" aria-hidden="true">
    <path d="M732 508 L780 400 Q787 385 806 385 L1080 385 L1080 508 Z" fill="var(--band)"/>
  </svg>
</section>

</body>
</html>
```